Lawn sign for construction company

Would like this to be a very clean and high end design for luxury homes. We need a yard sign designed that includes the company logo, website, phone number and major service offerings (residential and commercial renovations and maintenance)
The company website is brackwellbuilders.com all other contact info is in the attachments
Target Market(s)
Luxury home owners and business owners
Industry/Entity Type
Construction/Home Improvement
Font styles to use
Other font styles liked:
- See company logo and other graphics included for title text fonts. All other fonts can be standard sans serif.
Colors
0054AA
0677BA
7BADD7
CADEEF
E8F1F8
Requirements
Must have
- Clean, easy to read design, would like 2 sided sign. A main sign side and back side which states “free estimates, and includes the website and phone number. Must also match the color scheme of the provided logo and other company images. Dark Navy blue primary color, gray secondary color, and orange as an accent color.
Nice to have
- 2nd sign side very simple design
Should not have
- Too many graphics limit to 1-3 colors

```html
<!DOCTYPE html>
<html lang="en">
<head>
<meta charset="utf-8">
<title>Brackwell Builders – Yard Sign, Front and Back</title>
<link rel="stylesheet" href="https://fonts.googleapis.com/css2?family=Oswald:wght@500;600;700&family=Poppins:wght@400;700;800;900&display=swap">
<style>
  :root {
    --navy: #0b0a5c;
    --orange: #f26a1b;
    --orange-light: #fb8d3a;
    --orange-dark: #c8500f;
    --white: #ffffff;
    --ink: #141414;
    --backdrop: #ece7df;
  }
  * { box-sizing: border-box; margin: 0; padding: 0; }
  html, body { width: 1200px; height: 2848px; overflow: hidden; }
  body {
    background: var(--backdrop);
    display: flex;
    flex-direction: column;
    align-items: center;
    justify-content: center;
    gap: 30px;
    font-family: "Poppins", Arial, sans-serif;
  }
  .side-label {
    font-family: "Poppins", Arial, sans-serif;
    font-weight: 700;
    font-size: 80px;
    color: var(--ink);
    line-height: 1;
  }
  .side-label + .sign { margin-bottom: 120px; }
  .sign {
    position: relative;
    width: 1000px;
    height: 745px;
    background: var(--navy);
    box-shadow: 14px 18px 30px rgba(0,0,0,0.35);
    overflow: hidden;
  }
  .frame-outer, .frame-inner {
    position: absolute;
    border: 3px solid var(--white);
    pointer-events: none;
    z-index: 3;
  }
  .frame-outer { inset: 16px; }
  .frame-inner { inset: 26px; border-width: 2px; }

  /* Front */
  .brand {
    position: absolute;
    top: 120px; left: 0; right: 0;
    display: flex;
    align-items: center;
    justify-content: center;
    gap: 26px;
    color: var(--white);
    font-family: "Oswald", Arial, sans-serif;
    font-weight: 700;
  }
  .brand-dot {
    width: 96px; height: 96px;
    border-radius: 50%;
    background: var(--orange);
  }
  .brand-name { text-align: left; line-height: 1; }
  .brand-name .line-main { font-size: 84px; letter-spacing: 1px; }
  .brand-name .line-sub { font-size: 30px; letter-spacing: 26px; margin-top: 10px; }
  .headline {
    position: absolute;
    top: 410px; left: 0; right: 0;
    text-align: center;
    color: var(--white);
    font-weight: 800;
    font-size: 44px;
    line-height: 1.28;
    letter-spacing: 0.5px;
  }
  .service-band {
    position: absolute;
    left: 0; right: 0; bottom: 0;
    height: 158px;
    background: var(--orange);
  }
  .services {
    position: absolute;
    left: 30px; right: 30px; bottom: 40px;
    display: flex;
    z-index: 4;
  }
  .service {
    position: relative;
    display: flex;
    flex-direction: column;
    align-items: center;
    justify-content: flex-end;
    height: 150px;
  }
  .service:nth-child(1) { width: 350px; }
  .service:nth-child(2) { width: 374px; border-left: 3px solid var(--white); border-right: 3px solid var(--white); }
  .service:nth-child(3) { width: 210px; }
  .service:nth-child(2), .service:nth-child(3) { }
  .service-icon { width: 82px; height: 90px; margin-bottom: 12px; }
  .service-name {
    font-family: "Oswald", Arial, sans-serif;
    font-weight: 600;
    font-size: 32px;
    color: var(--white);
    letter-spacing: 0.5px;
    line-height: 1;
  }
  .service:nth-child(1) .service-icon { margin-left: -30px; }

  /* Back */
  .offer {
    position: absolute;
    top: 80px; left: 0; right: 0;
    text-align: center;
    font-weight: 900;
    font-size: 84px;
    line-height: 1;
    color: var(--white);
    letter-spacing: 1px;
  }
  .offer .accent { color: var(--orange); }
  .credential {
    position: absolute;
    top: 205px; left: 50%;
    transform: translateX(-50%);
    border: 3px solid var(--white);
    padding: 10px 22px;
    color: var(--white);
    font-weight: 700;
    font-size: 36px;
    letter-spacing: 1px;
    white-space: nowrap;
  }
  .phone-ribbon {
    position: absolute;
    top: 315px; left: 80px;
    width: 840px; height: 250px;
  }
  .website {
    position: absolute;
    top: 595px; left: 0; right: 0;
    text-align: center;
    color: var(--white);
    font-size: 46px;
    font-weight: 400;
    letter-spacing: 1px;
  }
</style>
</head>
<body>

  <h2 class="side-label">Front Side</h2>
  <section class="sign sign-front">
    <div class="frame-outer"></div>
    <div class="frame-inner"></div>

    <div class="brand">
      <span class="brand-dot"></span>
      <div class="brand-name">
        <div class="line-main">BRACKWELL BUILDERS</div>
        <div class="line-sub">COMPANY</div>
      </div>
    </div>

    <p class="headline">RESIDENTIAL AND COMMERCIAL<br>RENOVATIONS AND MAINTENANCE</p>

    <div class="service-band"></div>
    <ul class="services" style="list-style:none">
      <li class="service">
        <svg class="service-icon" viewBox="0 0 82 90" aria-hidden="true">
          <polygon points="41,2 79,23 79,67 41,88 3,67 3,23" fill="#fff" stroke="#f26a1b" stroke-width="3"/>
          <path d="M28 24 h20 l8 8 v34 h-28 z" fill="none" stroke="#141414" stroke-width="2.5" stroke-linejoin="round"/>
          <path d="M34 36 h16 M34 43 h16 M34 50 h12" stroke="#141414" stroke-width="2.5"/>
          <path d="M34 59 q3 -5 6 0 t6 0" fill="none" stroke="#141414" stroke-width="2"/>
        </svg>
        <span class="service-name">GENERAL CONTRACTING</span>
      </li>
      <li class="service">
        <svg class="service-icon" viewBox="0 0 82 90" aria-hidden="true">
          <polygon points="41,2 79,23 79,67 41,88 3,67 3,23" fill="#fff" stroke="#f26a1b" stroke-width="3"/>
          <rect x="38" y="22" width="22" height="28" fill="none" stroke="#141414" stroke-width="2.5"/>
          <path d="M43 30 h12 M43 36 h12 M43 42 h8" stroke="#141414" stroke-width="2"/>
          <path d="M22 56 l12 -10 l12 10 v12 h-24 z" fill="none" stroke="#141414" stroke-width="2.5" stroke-linejoin="round"/>
          <rect x="31" y="60" width="6" height="8" fill="#141414"/>
        </svg>
        <span class="service-name">PROPERTY MANAGEMENT</span>
      </li>
      <li class="service">
        <svg class="service-icon" viewBox="0 0 82 90" aria-hidden="true">
          <polygon points="41,2 79,23 79,67 41,88 3,67 3,23" fill="#fff" stroke="#f26a1b" stroke-width="3"/>
          <path d="M20 36 L62 28" stroke="#141414" stroke-width="3"/>
          <rect x="24" y="38" width="34" height="26" fill="none" stroke="#141414" stroke-width="2.5"/>
          <path d="M31 40 v24 M38 40 v24 M45 40 v24 M52 40 v24 M24 52 h34" stroke="#141414" stroke-width="2"/>
          <path d="M18 66 h46" stroke="#141414" stroke-width="3"/>
        </svg>
        <span class="service-name">REMODELING</span>
      </li>
    </ul>
  </section>

  <h2 class="side-label">Back Side</h2>
  <section class="sign sign-back">
    <div class="frame-outer"></div>
    <div class="frame-inner"></div>

    <h1 class="offer"><span class="accent">FREE</span> ESTIMATES</h1>
    <p class="credential">LICENSED &amp; INSURED</p>

    <svg class="phone-ribbon" viewBox="0 0 840 250" aria-label="Phone 555-204-7718">
      <defs>
        <linearGradient id="ribbonFill" x1="0" y1="0" x2="1" y2="0">
          <stop offset="0" stop-color="#f26a1b"/>
          <stop offset="0.5" stop-color="#fb8d3a"/>
          <stop offset="1" stop-color="#f26a1b"/>
        </linearGradient>
        <path id="ribbonArc" d="M120,140 Q420,40 720,140"/>
      </defs>
      <path d="M10,120 L120,95 L135,205 L50,225 L85,170 Z" fill="#f26a1b"/>
      <path d="M830,120 L720,95 L705,205 L790,225 L755,170 Z" fill="#f26a1b"/>
      <path d="M100,180 L135,205 L120,160 Z" fill="#c8500f"/>
      <path d="M740,180 L705,205 L720,160 Z" fill="#c8500f"/>
      <path d="M90,70 Q420,-20 750,70 L725,185 Q420,100 115,185 Z" fill="url(#ribbonFill)"/>
      <text font-family="Poppins, Arial, sans-serif" font-weight="800" font-size="74" fill="#fff" letter-spacing="2">
        <textPath href="#ribbonArc" startOffset="50%" text-anchor="middle">555-204-7718</textPath>
      </text>
    </svg>

    <p class="website">brackwellbuilders.com</p>
  </section>

</body>
</html>
```